Upscale and cool gun range / bar + lounge. Think axe throwing, but much cooler.

capture interest and make them want to know more.

s/b more on the cool and hip side to be on brand

will be offering a gift card. example attached

```html
<!DOCTYPE html>
<html lang="en">
<head>
<meta charset="utf-8">
<title>Ironsight – Airgun Range + Social Club</title>
<link rel="stylesheet" href="https://fonts.googleapis.com/css2?family=Montserrat:wght@500;700&family=Roboto+Condensed:wght@400;700&display=swap">
<style>
  :root {
    --amber: #f7a51e;
    --ink: #000000;
    --paper: #ffffff;
  }
  html, body {
    margin: 0;
    padding: 0;
    overflow: hidden;
  }
  .flyer {
    position: relative;
    width: 839px;
    height: 1200px;
    background: var(--amber);
    overflow: hidden;
    font-family: "Roboto Condensed", sans-serif;
  }
  .diagonal-band {
    position: absolute;
    inset: 0;
    width: 839px;
    height: 1200px;
  }
  .brand-name {
    position: absolute;
    left: 56px;
    top: 296px;
    margin: 0;
    font-family: "Montserrat", sans-serif;
    font-weight: 500;
    font-size: 33px;
    letter-spacing: 0.42em;
    color: var(--ink);
  }
  .tagline {
    position: absolute;
    left: 392px;
    top: 126px;
    width: 420px;
    margin: 0;
    font-family: "Montserrat", sans-serif;
    font-weight: 500;
    font-size: 26.5px;
    line-height: 33.7px;
    color: var(--ink);
  }
  .pricing {
    position: absolute;
    left: 55px;
    top: 532px;
    width: 340px;
    color: var(--paper);
  }
  .pricing-title {
    margin: 0 0 12px;
    font-weight: 700;
    font-size: 41px;
    line-height: 1;
    color: var(--amber);
  }
  .package {
    position: absolute;
    left: 0;
    margin: 0;
    font-size: 23px;
    line-height: 24.4px;
    text-transform: uppercase;
  }
  .package-name { font-weight: 700; display: block; }
  .package--agent    { top: 61px; }
  .package--commando { top: 157px; }
  .package--rancher  { top: 254px; }
  .package--hunter   { top: 374px; }
  .package--armorer  { top: 447px; }
  .website {
    position: absolute;
    left: 55px;
    top: 1108px;
    margin: 0;
    font-family: "Montserrat", sans-serif;
    font-weight: 700;
    font-size: 37px;
    color: var(--ink);
  }
  .hero-illustration {
    position: absolute;
    left: 385px;
    top: 475px;
    width: 420px;
    height: 725px;
    border-radius: 120px 120px 0 0;
    background: linear-gradient(160deg, #1a1a1a 0%, #2b2b2b 45%, #f2f2f2 70%, #1a1a1a 100%);
    box-shadow: 0 0 0 8px var(--amber);
  }
</style>
</head>
<body>
  <main class="flyer">
    <svg class="diagonal-band" viewBox="0 0 839 1200" aria-hidden="true">
      <polygon points="0,521 839,322 839,923 0,1104" fill="var(--ink)"/>
    </svg>

    <h1 class="brand-name">IRONSIGHT</h1>

    <p class="tagline">As the only Airgun Shooting Range + Social Club in North America, we can offer you an adrenaline rush that few other activities can compare to.</p>

    <section class="pricing">
      <h2 class="pricing-title">PRICING</h2>
      <p class="package package--agent"><span class="package-name">The Agent | $59.99</span>30 mins - rifle or pistol -<br>unlimited rounds</p>
      <p class="package package--commando"><span class="package-name">The Commando | $109.00</span>60 mins - rifle or pistol -<br>unlimited rounds</p>
      <p class="package package--rancher"><span class="package-name">The Rancher | $139.00</span>60 mins - rifle or pistol -<br>unlimited rounds<br>air javelin: 6 arrows</p>
      <p class="package package--hunter"><span class="package-name">The Big Game Hunter | $25.00</span>air javelin - 10 arrows</p>
      <p class="package package--armorer"><span class="package-name">The Armorer | $40</span>30 mins - rifle or pistol -<br>unlimited rounds</p>
    </section>

    <div class="hero-illustration" role="img" aria-label="Stylised black and white illustration of a cat-headed woman aiming a pistol, outlined in amber"></div>

    <p class="website">www.ironsight.ca</p>
  </main>
</body>
</html>
```